Musical download and streaming website

hello designers, I want to start up a musical website where users can download and rate music of different genres such as RnB, Hip hop, rock, afro-pop. This website should be attractive and contemporary. There will be a search column for different songs. Music files will be mp3, mwa, and others. I like blue, gold, pink and indigo colors. My website should resemble http://tunovalt.com. There should be good imaginary of music stars on my website.

```html
<!DOCTYPE html>
<html lang="en">
<head>
<meta charset="utf-8">
<title>Cadence Music</title>
<link href="https://fonts.googleapis.com/css2?family=Roboto:wght@400;500;700&family=Roboto+Condensed:wght@400;700&display=swap" rel="stylesheet">
<style>
:root{
  --night:#1a1630;
  --ink:#141a2c;
  --row:#161b2b;
  --row-line:#232a3d;
  --blue:#2e8bc9;
  --gold:#f2b51c;
  --pink:#e02b88;
  --white:#ffffff;
  --muted:#c9c6d6;
  --player:#1b2233;
}
*{margin:0;padding:0;box-sizing:border-box}
html,body{width:913px;height:1200px;overflow:hidden}
body{
  position:relative;
  font-family:"Roboto",sans-serif;color:var(--white);
  background:
    radial-gradient(ellipse 420px 300px at 450px 1000px,rgba(214,120,90,.55),transparent 70%),
    radial-gradient(ellipse 500px 400px at 200px 300px,rgba(120,40,110,.55),transparent 70%),
    radial-gradient(ellipse 500px 420px at 800px 700px,rgba(90,40,120,.5),transparent 70%),
    linear-gradient(180deg,#2a1a3a 0%,#241a3e 45%,#3a2040 85%,#2a1830 100%);
}
.abs{position:absolute}

/* header */
.brand{left:70px;top:32px;display:flex;align-items:center;gap:8px}
.brand-dot{width:16px;height:16px;border-radius:50%;background:var(--pink)}
.brand-name{font-family:"Roboto Condensed",sans-serif;font-weight:700;font-size:25px;color:var(--white);letter-spacing:.5px}
.nav{top:36px;left:384px}
.nav a{position:absolute;color:var(--white);text-decoration:none;font-size:12.5px;white-space:nowrap}
.social{left:758px;top:36px;display:flex;gap:9px}
.social span{width:15px;height:15px;border-radius:2px;background:var(--white)}

/* hero */
.hero{left:66px;top:78px;width:780px;height:372px;
  background:linear-gradient(120deg,#8a6a5c 0%,#c9b5a8 35%,#e8dcd8 60%,#a9b3be 100%)}
.hero-title{left:103px;top:380px;font-family:"Roboto Condensed",sans-serif;font-weight:700;font-size:36px;letter-spacing:-.5px;text-shadow:0 1px 3px rgba(0,0,0,.4)}
.hero-arrow{top:388px;width:26px;height:26px;border-radius:50%;background:rgba(90,90,90,.6);display:flex;align-items:center;justify-content:center}

/* players */
.panel{top:450px;height:91px}
.panel.blue{left:65px;width:392px;background:var(--blue)}
.panel.gold{left:457px;width:391px;background:var(--gold)}
.panel-title{position:absolute;left:18px;top:13px;font-size:13px;text-transform:uppercase;font-weight:400}
.panel.gold .panel-title{left:16px}
.player{position:absolute;left:13px;top:39px;width:358px;height:29px;background:var(--player);border-radius:4px;box-shadow:0 2px 4px rgba(0,0,0,.35)}
.player svg{position:absolute;left:0;top:0}

/* filter */
.filter{left:65px;top:541px;width:783px;height:69px;background:var(--ink)}
.tabs{position:absolute;left:27px;top:30px}
.tabs span{position:absolute;font-size:13px;white-space:nowrap;color:var(--white)}
.tabs .on{text-decoration:underline}
.search{position:absolute;left:397px;top:17px;width:264px;height:35px;background:var(--white);border-radius:2px;color:#555;font-size:10px;padding:12px 0 0 13px}
.search-btn{position:absolute;left:666px;top:17px;width:103px;height:35px;background:var(--pink);border-radius:2px;font-size:13px;text-align:center;line-height:35px;font-weight:500}

/* charts */
.sec-title{top:632px;font-size:18px;font-weight:400}
.see-all{top:639px;font-size:9.5px}
.chart{top:666px;width:385px;height:304px;background:var(--row)}
.chart.left{left:66px}
.chart.right{left:463px}
.row{height:60.8px;border-bottom:1px solid var(--row-line);position:relative}
.row:last-child{border-bottom:none}
.row .ico{position:absolute;left:8px;top:11px;width:32px;height:32px;display:flex;align-items:center;justify-content:center}
.left .ico{background:var(--pink)}
.right .ico{background:var(--gold)}
.row .t1{position:absolute;left:54px;top:13px;font-size:10.5px;white-space:nowrap}
.row .t2{position:absolute;left:54px;top:31px;font-size:8.5px;font-weight:500;white-space:nowrap}
.row .dur{position:absolute;left:250px;top:21px;font-size:9.5px}
.row .acts{position:absolute;left:305px;top:20px}

/* footer */
.f-head{top:1022px;font-size:12.5px;text-transform:uppercase;font-weight:400}
.f-links{left:71px;top:1050px;list-style:none;font-size:8.5px;line-height:18.5px}
.f-links li::before{content:"";display:inline-block;border-left:4px solid var(--white);border-top:3px solid transparent;border-bottom:3px solid transparent;margin-right:5px}
.f-text{font-size:8.5px;line-height:13px;color:var(--white)}
.about{left:226px;top:1051px;width:186px;text-align:justify}
.about p+p{margin-top:5px}
.contact{left:497px;top:1052px;line-height:15.5px}
.contact p{margin-bottom:3px}
.news{left:692px;top:1051px;width:150px}
.email{left:692px;top:1082px;width:111px;height:23px;background:#f3f3f3;color:#666;font-size:8.5px;padding:6px 0 0 10px}
.submit{left:803px;top:1082px;width:43px;height:23px;background:var(--gold);font-size:9px;text-align:center;line-height:23px}
.bottom{left:0;top:1142px;width:913px;height:58px;background:#0b0b0d;text-align:center;font-size:8.5px;line-height:58px}
</style>
</head>
<body>

<svg width="0" height="0" style="position:absolute">
  <defs>
    <symbol id="player-bar" viewBox="0 0 358 29">
      <g fill="#fff">
        <path d="M18 10l-6 4.5 6 4.5zM25 10l-6 4.5 6 4.5z"/>
        <path d="M38 10l6 4.5-6 4.5z"/>
        <path d="M57 10l6 4.5-6 4.5zM64 10l6 4.5-6 4.5z"/>
      </g>
      <line x1="85" y1="14.5" x2="229" y2="14.5" stroke="#4a5265" stroke-width="2"/>
      <line x1="85" y1="14.5" x2="182" y2="14.5" stroke="#fff" stroke-width="2"/>
      <circle cx="182" cy="14.5" r="4" fill="#1b2233" stroke="#fff" stroke-width="1.6"/>
      <text x="242" y="17.5" font-size="7.5" fill="#fff" font-family="Roboto,sans-serif">2:11 / 3:28</text>
      <path d="M293 12.5h2l3-3v10l-3-3h-2z" fill="#fff"/>
      <path d="M300 11.5q2.5 3 0 6" stroke="#fff" fill="none"/>
      <line x1="311" y1="14.5" x2="342" y2="14.5" stroke="#4a5265" stroke-width="2"/>
      <line x1="311" y1="14.5" x2="332" y2="14.5" stroke="#fff" stroke-width="2"/>
    </symbol>
    <symbol id="headphones" viewBox="0 0 16 16"><path d="M2.5 11V8a5.5 5.5 0 0 1 11 0v3" stroke="#fff" stroke-width="2" fill="none"/><rect x="1.5" y="9.5" width="3.5" height="4.5" rx="1" fill="#fff"/><rect x="11" y="9.5" width="3.5" height="4.5" rx="1" fill="#fff"/></symbol>
    <symbol id="actions" viewBox="0 0 72 14">
      <path d="M7 0.5l2 4.3 4.6.5-3.5 3.1 1 4.6L7 10.6 2.9 13l1-4.6L.4 5.3 5 4.8z" fill="#f2c318"/>
      <circle cx="34" cy="7" r="6.3" fill="#fff"/><path d="M32 4v6l4.8-3z" fill="#161b2b"/>
      <path d="M57 12h10a3.2 3.2 0 0 0 .3-6.4A4.6 4.6 0 0 0 58.6 4.6 3.7 3.7 0 0 0 57 12z" fill="#fff"/>
      <path d="M62 5.5v4.5M59.8 8l2.2 2.3 2.2-2.3" stroke="#161b2b" stroke-width="1.4" fill="none"/>
    </symbol>
  </defs>
</svg>

<header>
  <div class="abs brand"><span class="brand-dot"></span><span class="brand-name">Cadence Music</span></div>
  <nav class="abs nav">
    <a style="left:0">HOME</a>
    <a style="left:72px">CATEGORIES</a>
    <a style="left:177px">COLLECTIONS</a>
    <a style="left:289px">TOP TENS</a>
  </nav>
  <div class="abs social" aria-label="Social links"><span></span><span></span><span></span><span></span></div>
</header>

<section>
  <div class="abs hero" role="img" aria-label="Photo of a hand holding a smartphone playing music beside a laptop"></div>
  <h1 class="abs hero-title">CADENCE MUSIC DOWNLOAD</h1>
  <div class="abs hero-arrow" style="left:763px"><svg width="10" height="12" viewBox="0 0 10 12"><path d="M7 1 2 6l5 5" stroke="#fff" stroke-width="2" fill="none"/></svg></div>
  <div class="abs hero-arrow" style="left:793px"><svg width="10" height="12" viewBox="0 0 10 12"><path d="M3 1l5 5-5 5" stroke="#fff" stroke-width="2" fill="none"/></svg></div>
</section>

<section>
  <div class="abs panel blue">
    <div class="panel-title">Feature Play List</div>
    <div class="player"><svg width="358" height="29"><use href="#player-bar"/></svg></div>
  </div>
  <div class="abs panel gold">
    <div class="panel-title">Popular Last Added</div>
    <div class="player" style="left:12px"><svg width="358" height="29"><use href="#player-bar"/></svg></div>
  </div>
</section>

<section class="abs filter">
  <div class="tabs">
    <span class="on" style="left:0">All</span>
    <span style="left:37px">Song</span>
    <span style="left:89px">Artist</span>
    <span style="left:142px">RnB</span>
    <span style="left:189px">Hip hop</span>
    <span style="left:254px">rock</span>
    <span style="left:302px">afro-pop</span>
  </div>
  <div class="search">Enter Search Text Here</div>
  <div class="search-btn">SEARCH</div>
</section>

<section>
  <h2 class="abs sec-title" style="left:71px">TOP 20 ARTISTS</h2>
  <span class="abs see-all" style="left:398px">See All &gt;&gt;</span>
  <div class="abs chart left">
    <div class="row"><div class="ico"><svg width="16" height="16"><use href="#headphones"/></svg></div><div class="t1">SED UT PERSPICIATIS UNDE OMNIS</div><div class="t2">Nemo enim ipsam voluptatem quia</div><div class="dur">00.25</div><svg class="acts" width="72" height="14"><use href="#actions"/></svg></div>
    <div class="row"><div class="ico"><svg width="16" height="16"><use href="#headphones"/></svg></div><div class="t1">SED UT PERSPICIATIS UNDE OMNIS</div><div class="t2">Nemo enim ipsam voluptatem quia</div><div class="dur">00.25</div><svg class="acts" width="72" height="14"><use href="#actions"/></svg></div>
    <div class="row"><div class="ico"><svg width="16" height="16"><use href="#headphones"/></svg></div><div class="t1">SED UT PERSPICIATIS UNDE OMNIS</div><div class="t2">Nemo enim ipsam voluptatem quia</div><div class="dur">00.25</div><svg class="acts" width="72" height="14"><use href="#actions"/></svg></div>
    <div class="row"><div class="ico"><svg width="16" height="16"><use href="#headphones"/></svg></div><div class="t1">SED UT PERSPICIATIS UNDE OMNIS</div><div class="t2">Nemo enim ipsam voluptatem quia</div><div class="dur">00.25</div><svg class="acts" width="72" height="14"><use href="#actions"/></svg></div>
    <div class="row"><div class="ico"><svg width="16" height="16"><use href="#headphones"/></svg></div><div class="t1">SED UT PERSPICIATIS UNDE OMNIS</div><div class="t2">Nemo enim ipsam voluptatem quia</div><div class="dur">00.25</div><svg class="acts" width="72" height="14"><use href="#actions"/></svg></div>
  </div>

  <h2 class="abs sec-title" style="left:479px">TOP 20 SONGS</h2>
  <span class="abs see-all" style="left:806px">See All &gt;&gt;</span>
  <div class="abs chart right">
    <div class="row"><div class="ico"><svg width="16" height="16"><use href="#headphones"/></svg></div><div class="t1">SED UT PERSPICIATIS UNDE OMNIS</div><div class="t2">Nemo enim ipsam voluptatem quia</div><div class="dur">00.25</div><svg class="acts" width="72" height="14"><use href="#actions"/></svg></div>
    <div class="row"><div class="ico"><svg width="16" height="16"><use href="#headphones"/></svg></div><div class="t1">SED UT PERSPICIATIS UNDE OMNIS</div><div class="t2">Nemo enim ipsam voluptatem quia</div><div class="dur">00.25</div><svg class="acts" width="72" height="14"><use href="#actions"/></svg></div>
    <div class="row"><div class="ico"><svg width="16" height="16"><use href="#headphones"/></svg></div><div class="t1">SED UT PERSPICIATIS UNDE OMNIS</div><div class="t2">Nemo enim ipsam voluptatem quia</div><div class="dur">00.25</div><svg class="acts" width="72" height="14"><use href="#actions"/></svg></div>
    <div class="row"><div class="ico"><svg width="16" height="16"><use href="#headphones"/></svg></div><div class="t1">SED UT PERSPICIATIS UNDE OMNIS</div><div class="t2">Nemo enim ipsam voluptatem quia</div><div class="dur">00.25</div><svg class="acts" width="72" height="14"><use href="#actions"/></svg></div>
    <div class="row"><div class="ico"><svg width="16" height="16"><use href="#headphones"/></svg></div><div class="t1">SED UT PERSPICIATIS UNDE OMNIS</div><div class="t2">Nemo enim ipsam voluptatem quia</div><div class="dur">00.25</div><svg class="acts" width="72" height="14"><use href="#actions"/></svg></div>
  </div>
</section>

<footer>
  <h3 class="abs f-head" style="left:71px">Links</h3>
  <ul class="abs f-links">
    <li>WHAT WE OFFER</li>
    <li>POPULAR MUSIC</li>
    <li>FEATURE PLAY LIST</li>
    <li>ABOUT US</li>
  </ul>
  <h3 class="abs f-head" style="left:226px">Neque Porro Quisquam</h3>
  <div class="abs f-text about">
    <p>Lorem Ipsum has been the industry's standard dummy text ever since the 1500s, when an unknown printer took a galley of type</p>
    <p>It has survived not only five centuries, but also the leap into electronic typesetting, remaining</p>
  </div>
  <h3 class="abs f-head" style="left:497px">Get In Touch</h3>
  <div class="abs f-text contact">
    <p>Address : 1200 Harbor Lane Ave,<br>Westfield Park, NJ</p>
    <p>Phone : (555)0142876</p>
    <p>Email : info@cadencemusic.example</p>
  </div>
  <h3 class="abs f-head" style="left:692px">Newsletter</h3>
  <p class="abs f-text news">Your about us information would fit here nicely.</p>
  <div class="abs email">Email address</div>
  <div class="abs submit">Submit</div>
  <div class="abs bottom">Copyright © 2016. All Rights Reserved</div>
</footer>

</body>
</html>
```